QP Fiduciary Website Redesign Contest

We want to refresh our website to be more insitutional, professional for an international audience. We have designed a new logo for this purpose and that has been attached. A full brand brief and positioning statement has also been attached. Please read through all the documents carefully before designing. The old website is found here: https://qp-fiduciary.example/

Target Market(s)

Actuaries and associated businesses internationally

Industry/Entity Type

professional services - actuaries

Number of Pages Required

3 page

Font styles to use
Sans Serif

Colors
0054AA
0677BA
7BADD7
CADEEF
E8F1F8
0094D4
00A9DD
6FCCEA
C7EBF8
E9F6FB
F0912C
F2A743
F7CA91
FBE8D2
FDF5EE
EE7325
F08F49
F5BC92
FAE3D3
FDF4ED
EB3D1F
EC4F4E
F09395
F8D3D4
FCEDEE

Requirements
Must have
• blues and greens to match the logo color, complimentary colors, navigation
Nice to have
• old site: https://qp-fiduciary.example/

```html
<!DOCTYPE html>
<html lang="en">
<head>
<meta charset="utf-8">
<title>QP Fiduciary — Actuarial Software</title>
<link href="https://fonts.googleapis.com/css2?family=Inter:wght@400;500;600;700&family=Orbitron:wght@400;500;800&display=swap" rel="stylesheet">
<style>
:root{
  --primary:#0054AA;
  --primary-2:#0677BA;
  --accent:#0094D4;
  --accent-2:#00A9DD;
  --sky:#7BADD7;
  --sky-soft:#CADEEF;
  --cyan-soft:#C7EBF8;
  --tint:#E8F1F8;
  --ink:#0d1b2e;
  --text:#33404f;
  --muted:#56647a;
  --navy:#0a2a4f;
  --navy-2:#071d38;
  --white:#ffffff;
}
*{box-sizing:border-box;margin:0;padding:0}
html,body{width:1200px;height:4098px;overflow:hidden}
body{font-family:"Inter",Arial,sans-serif;color:var(--text);background:var(--white);position:relative}
.abs{position:absolute}
a{color:inherit;text-decoration:none}

/* header */
.site-header{position:absolute;top:0;left:0;width:1200px;height:70px;background:var(--white)}
.brand{position:absolute;left:70px;top:19px;display:flex;align-items:center;gap:10px;font-weight:700;font-size:25px;color:var(--primary);letter-spacing:.5px}
.brand-dot{width:20px;height:20px;border-radius:50%;background:var(--accent)}
.main-nav{position:absolute;left:390px;top:26px;display:flex;gap:33px;font-size:13px;color:#333}
.main-nav .active{color:var(--accent)}
.btn{display:inline-flex;align-items:center;gap:14px;background:var(--primary);color:var(--white);font-weight:600;border-radius:24px;font-size:14px}
.btn-arrow{width:30px;height:30px;border-radius:50%;border:2px solid var(--white);display:flex;align-items:center;justify-content:center}
.header-cta{position:absolute;left:882px;top:16px;height:38px;width:246px;justify-content:center;font-size:13px;border-radius:19px}

/* hero */
.hero{position:absolute;top:70px;left:0;width:1200px;height:544px;background:linear-gradient(90deg,var(--navy-2) 0%,var(--navy) 40%,var(--primary-2) 62%,var(--sky) 100%)}
.hero-title{position:absolute;left:70px;top:120px;font-family:"Orbitron",sans-serif;font-size:34px;line-height:42px;color:var(--white);font-weight:400;letter-spacing:1px}
.hero-title b{font-weight:800}
.hero-text{position:absolute;left:72px;top:302px;width:470px;font-size:14px;line-height:22px;color:#e6eef7}
.hero-text b{color:var(--white)}
.hero-cta{position:absolute;left:70px;top:374px;height:44px;padding:0 6px 0 24px;background:var(--accent)}

/* section titles */
.sec-title{position:absolute;left:0;width:1200px;text-align:center;font-family:"Orbitron",sans-serif;font-size:35px;font-weight:800;color:var(--ink);letter-spacing:1px}
.sec-title span{color:var(--accent);font-weight:500}
.sec-rule{position:absolute;left:578px;width:44px;height:2px;background:var(--primary)}
.sec-sub{position:absolute;left:0;width:1200px;text-align:center;font-size:14px;line-height:23px;color:#333}

/* overview */
.feature-card{position:absolute;width:215px;height:254px;background:var(--white);border-radius:6px;box-shadow:0 4px 18px rgba(0,40,90,.09);padding:30px 22px}
.feature-card svg{width:54px;height:54px}
.feature-card h3{margin-top:22px;font-size:15px;font-weight:600;color:var(--ink);line-height:21px;min-height:42px}
.feature-card .rule{width:30px;height:2px;background:var(--accent);margin:18px 0}
.feature-card p{font-size:12.5px;line-height:19px;color:var(--muted)}

/* core */
.core{position:absolute;top:1167px;left:0;width:1200px;height:682px;background:var(--tint)}
.core-photo{position:absolute;left:142px;top:197px;width:423px;height:399px;border-radius:10px;background:linear-gradient(135deg,#1e2f46,#4d6683 55%,#c9b48c)}
.solution{position:absolute;left:629px;width:460px}
.solution .ico{position:absolute;left:0;top:0;width:70px;height:70px;border-radius:50%;display:flex;align-items:center;justify-content:center}
.solution .body{position:absolute;left:92px;top:0;width:370px}
.solution h3{font-size:15px;font-weight:600;color:var(--ink)}
.solution p{font-size:12.5px;line-height:19px;color:var(--muted);margin-top:8px}
.learn{display:inline-flex;align-items:center;gap:10px;margin-top:10px;color:var(--primary-2);font-size:12.5px}

/* characteristics */
.char-ring{position:absolute;left:425px;top:2055px;width:350px;height:350px;border-radius:50%;border:2px solid var(--sky)}
.char-logo{position:absolute;left:465px;top:2214px;width:270px;display:flex;align-items:center;justify-content:center;gap:10px;font-weight:700;font-size:28px;color:var(--primary)}
.char-ico{position:absolute;width:76px;height:76px;border-radius:50%;display:flex;align-items:center;justify-content:center;border:4px solid var(--white);box-shadow:0 0 0 1px var(--sky-soft)}
.char-item{position:absolute;width:280px}
.char-item h3{font-size:15px;font-weight:600;color:var(--ink)}
.char-item p{font-size:12.5px;line-height:19px;color:var(--muted);margin-top:6px}
.char-item.left{text-align:right}
.center-cta{position:absolute;height:44px;padding:0 6px 0 24px}

/* insights */
.insights{position:absolute;top:2575px;left:0;width:1200px;height:684px;background:var(--tint)}
.post{position:absolute;top:153px;width:286px;height:366px;background:var(--white);border-radius:6px;overflow:hidden;box-shadow:0 4px 14px rgba(0,40,90,.06)}
.post .thumb{height:191px}
.post .body{padding:20px 19px}
.post h3{font-size:15px;line-height:21px;font-weight:600;color:var(--ink)}
.post p{font-size:12.5px;line-height:19px;color:var(--muted);margin-top:8px}

/* cta */
.cta-box{position:absolute;left:142px;top:3345px;width:916px;height:376px;border-radius:18px;background:linear-gradient(120deg,#0b3a6e 0%,var(--navy) 45%,var(--navy-2) 100%);z-index:2}
.cta-title{position:absolute;top:84px;width:916px;text-align:center;font-family:"Orbitron",sans-serif;font-size:33px;line-height:43px;color:var(--white);font-weight:400;letter-spacing:1px}
.cta-title b{font-weight:800}
.cta-text{position:absolute;top:185px;width:916px;text-align:center;font-size:14px;line-height:23px;color:#e6eef7}
.cta-box .btn{background:var(--accent)}

/* footer */
.site-footer{position:absolute;top:3614px;left:0;width:1200px;height:484px;background:var(--navy-2)}
.foot-brand{position:absolute;left:142px;top:200px;display:flex;align-items:center;gap:12px;font-weight:700;font-size:32px;color:var(--white)}
.foot-about{position:absolute;left:142px;top:272px;width:300px;font-size:12.5px;line-height:19px;color:#d5e1ee}
.foot-head{position:absolute;font-family:"Orbitron",sans-serif;font-size:16px;color:var(--white);letter-spacing:1px}
.foot-links{position:absolute;left:576px;top:248px;list-style:none;font-size:12.5px;color:#d5e1ee;line-height:27.5px}
.contact-row{position:absolute;left:813px;display:flex;gap:14px;font-size:12.5px;line-height:19px;color:#d5e1ee}
.contact-row svg{flex:none;margin-top:2px}
.foot-rule{position:absolute;left:142px;top:422px;width:916px;height:1px;background:#24406a}
.foot-bottom{position:absolute;left:142px;top:452px;font-size:12px;color:#d5e1ee}
.socials{position:absolute;left:948px;top:443px;display:flex;gap:8px}
.socials span{width:30px;height:30px;border-radius:50%;background:var(--white);display:block}
.socials span+span{background:transparent;border:1.5px solid var(--white)}
</style>
</head>
<body>

<header class="site-header">
  <div class="brand"><span class="brand-dot"></span>QP Fiduciary</div>
  <nav class="main-nav">
    <a class="active">Home</a><a>Platform</a><a>Solutions</a><a>Insights</a><a>Company</a><a>Contact</a>
  </nav>
  <a class="btn header-cta">Request a Technical Walkthrough</a>
</header>

<section class="hero">
  <div class="abs" role="img" aria-label="Photo of three smiling professionals with tablets in a bright modern office" style="left:460px;top:0;width:740px;height:544px;background:linear-gradient(90deg,rgba(10,42,79,0) 0%,rgba(6,119,186,.55) 35%,rgba(123,173,215,.85) 75%,#CADEEF 100%)"></div>
  <h1 class="hero-title">ACTUARIAL SOFTWARE<br>FOR <b>STRUCTURED,<br>AUDITABLE FINANCIAL<br>ANALYSIS.</b></h1>
  <p class="hero-text"><b>QP Fiduciary</b> develops software that translates established actuarial methodologies into disciplined, decision-ready tools.</p>
  <a class="btn hero-cta">Request A Technical Walkthrough <span class="btn-arrow"><svg width="14" height="14" viewBox="0 0 14 14"><path d="M2 7h10M8 3l4 4-4 4" stroke="#fff" stroke-width="1.8" fill="none"/></svg></span></a>
</section>

<!-- overview -->
<h2 class="sec-title" style="top:683px">PLATFORM <span>OVERVIEW</span></h2>
<div class="sec-rule" style="top:735px"></div>
<p class="sec-sub" style="top:754px">Our platform empowers actuaries and risk professionals with tools designed for modern<br>regulatory and business demands.</p>

<div class="feature-card" style="left:142px;top:828px">
  <svg viewBox="0 0 54 54"><rect x="6" y="8" width="40" height="30" rx="2" fill="none" stroke="#0054AA" stroke-width="2"/><circle cx="26" cy="17" r="4" fill="none" stroke="#0054AA" stroke-width="2"/><path d="M26 21v5M16 26h20M16 26v5M26 26v5M36 26v5" stroke="#0054AA" stroke-width="2"/><path d="M20 38l-4 8M32 38l4 8" stroke="#0054AA" stroke-width="2"/></svg>
  <h3>Structured Workflows</h3><div class="rule"></div>
  <p>that guide users through every step of the analysis process</p>
</div>
<div class="feature-card" style="left:376px;top:828px">
  <svg viewBox="0 0 54 54"><circle cx="26" cy="28" r="20" fill="#C7EBF8"/><circle cx="30" cy="22" r="16" fill="none" stroke="#0094D4" stroke-width="2"/><path d="M20 16l16 16M18 22l14 14M24 12l16 16" stroke="#0094D4" stroke-width="2"/></svg>
  <h3>Full Transparency Of Assumptions</h3><div class="rule"></div>
  <p>that guide users through every step of the analysis process</p>
</div>
<div class="feature-card" style="left:567px;top:855px">
  <svg viewBox="0 0 54 54"><circle cx="14" cy="40" r="12" fill="#CADEEF"/><rect x="10" y="6" width="26" height="34" rx="2" fill="none" stroke="#0054AA" stroke-width="2"/><path d="M15 14h16M15 20h12M15 26h10" stroke="#0054AA" stroke-width="2"/><circle cx="34" cy="30" r="8" fill="#fff" stroke="#0054AA" stroke-width="2"/><path d="M40 36l6 6" stroke="#0054AA" stroke-width="3"/></svg>
  <h3>Built-in Auditability</h3><div class="rule"></div>
  <p>that guide users through every step of the analysis process</p>
</div>
<div class="feature-card" style="left:843px;top:828px">
  <svg viewBox="0 0 54 54"><circle cx="26" cy="26" r="22" fill="none" stroke="#0094D4" stroke-width="2"/><circle cx="26" cy="26" r="15" fill="#C7EBF8" stroke="#0094D4" stroke-width="2"/><path d="M18 22l8-5 8 5zM19 24v8M24 24v8M29 24v8M34 24v8M17 34h18" stroke="#0094D4" stroke-width="2" fill="none"/></svg>
  <h3>Robust Governance Features</h3><div class="rule"></div>
  <p>that guide users through every step of the analysis process</p>
</div>

<!-- core solutions -->
<section class="core">
  <h2 class="sec-title" style="top:70px">CORE <span>SOLUTIONS</span></h2>
  <div class="sec-rule" style="top:120px"></div>
  <p class="sec-sub" style="top:140px">Precision-built modules for the most demanding actuarial tasks</p>
  <div class="core-photo" role="img" aria-label="Photo of two hands joining puzzle pieces"></div>

  <div class="solution" style="top:197px">
    <div class="ico" style="background:var(--primary)"><svg width="36" height="36" viewBox="0 0 36 36"><circle cx="20" cy="12" r="7" fill="none" stroke="#fff" stroke-width="2"/><path d="M20 5v7h7" stroke="#fff" stroke-width="2" fill="none"/><path d="M4 26h8l6 3 10-4" stroke="#fff" stroke-width="2" fill="none"/></svg></div>
    <div class="body"><h3>Reserving &amp; Valuation</h3><p>Perform compliant, repeatable reserving and valuation processes with full traceability and support for multiple actuarial methods and regulatory frameworks.</p><a class="learn">Learn More <svg width="16" height="10" viewBox="0 0 16 10"><path d="M1 5h13M10 1l4 4-4 4" stroke="#0677BA" stroke-width="1.6" fill="none"/></svg></a></div>
  </div>
  <div class="solution" style="top:345px">
    <div class="ico" style="background:var(--accent)"><svg width="36" height="36" viewBox="0 0 36 36"><path d="M9 4h12l6 6v20H9z" fill="none" stroke="#fff" stroke-width="2"/><path d="M13 14h10M13 19h6" stroke="#fff" stroke-width="2"/><circle cx="24" cy="25" r="6" fill="#0094D4" stroke="#fff" stroke-width="2"/><path d="M24 21v8" stroke="#fff" stroke-width="1.5"/></svg></div>
    <div class="body"><h3>Pricing</h3><p>Build and test pricing models with transparent assumptions, scenario testing, and comparative analytics to support profitable product development.</p><a class="learn">Learn More <svg width="16" height="10" viewBox="0 0 16 10"><path d="M1 5h13M10 1l4 4-4 4" stroke="#0677BA" stroke-width="1.6" fill="none"/></svg></a></div>
  </div>
  <div class="solution" style="top:493px">
    <div class="ico" style="background:var(--primary)"><svg width="36" height="36" viewBox="0 0 36 36"><circle cx="18" cy="14" r="9" fill="none" stroke="#fff" stroke-width="2"/><path d="M18 9v6M18 18v1" stroke="#fff" stroke-width="2"/><path d="M4 28h9l6 3 12-5" stroke="#fff" stroke-width="2" fill="none"/></svg></div>
    <div class="body"><h3>Enterprise Risk Management</h3><p>Integrate risk metrics, stress testing, and capital modeling in a governed environment to support ORSA, Solvency II, and other ERM requirements.</p><a class="learn">Learn More <svg width="16" height="10" viewBox="0 0 16 10"><path d="M1 5h13M10 1l4 4-4 4" stroke="#0677BA" stroke-width="1.6" fill="none"/></svg></a></div>
  </div>
</section>

<!-- characteristics -->
<h2 class="sec-title" style="top:1915px">PLATFORM <span>CHARACTERISTICS</span></h2>
<div class="sec-rule" style="top:1970px"></div>
<p class="sec-sub" style="top:1991px">Engineered for clarity, built to scale across borders</p>

<div class="char-ring"></div>
<div class="char-logo"><span class="brand-dot"></span>QP Fiduciary</div>

<div class="char-ico" style="left:444px;top:2075px;background:var(--primary)"><svg width="38" height="38" viewBox="0 0 38 38"><circle cx="19" cy="9" r="4" fill="none" stroke="#fff" stroke-width="2"/><path d="M19 13v6M9 19h20M9 19v6M19 19v6M29 19v6" stroke="#fff" stroke-width="2"/><rect x="5" y="25" width="8" height="7" fill="none" stroke="#fff" stroke-width="2"/><rect x="15" y="25" width="8" height="7" fill="none" stroke="#fff" stroke-width="2"/><rect x="25" y="25" width="8" height="7" fill="none" stroke="#fff" stroke-width="2"/></svg></div>
<div class="char-ico" style="left:678px;top:2075px;background:var(--accent)"><svg width="38" height="38" viewBox="0 0 38 38"><circle cx="13" cy="12" r="7" fill="none" stroke="#fff" stroke-width="2"/><circle cx="26" cy="15" r="4" fill="none" stroke="#fff" stroke-width="2"/><path d="M18 27c2-5 14-5 16 0M4 28h8l6 3 8-2" stroke="#fff" stroke-width="2" fill="none"/></svg></div>
<div class="char-ico" style="left:444px;top:2308px;background:var(--accent)"><svg width="38" height="38" viewBox="0 0 38 38"><path d="M9 5h14l6 6v22H9z" fill="none" stroke="#fff" stroke-width="2"/><circle cx="18" cy="20" r="6" fill="none" stroke="#fff" stroke-width="2"/><path d="M22 24l6 6" stroke="#fff" stroke-width="2.5"/></svg></div>
<div class="char-ico" style="left:678px;top:2308px;background:var(--primary)"><svg width="38" height="38" viewBox="0 0 38 38"><circle cx="18" cy="16" r="10" fill="none" stroke="#fff" stroke-width="2"/><path d="M14 20v-5M18 20v-8M22 20v-3" stroke="#fff" stroke-width="2"/><path d="M5 32l8-6 5 3 12-8" stroke="#fff" stroke-width="2" fill="none"/></svg></div>

<div class="char-item left" style="left:138px;top:2082px"><h3>Structured Workflows</h3><p>Consistent, repeatable processes from<br>data to disclosure.</p></div>
<div class="char-item" style="left:781px;top:2082px"><h3>Multi-jurisdictional Review Support</h3><p>Localise assumptions, outputs, and reports<br>for any regulator.</p></div>
<div class="char-item left" style="left:138px;top:2315px"><h3>Transparent Assumptions</h3><p>Every assumption exposed, documented,<br>and linked to source.</p></div>
<div class="char-item" style="left:781px;top:2315px"><h3>Comparative Analysis Capability</h3><p>Run scenarios side by side — instantly see<br>impacts.</p></div>

<a class="btn center-cta" style="left:449px;top:2448px">Request A Technical Walkthrough <span class="btn-arrow"><svg width="14" height="14" viewBox="0 0 14 14"><path d="M2 7h10M8 3l4 4-4 4" stroke="#fff" stroke-width="1.8" fill="none"/></svg></span></a>

<!-- insights -->
<section class="insights">
  <h2 class="sec-title" style="top:73px">LATEST <span>INSIGHTS</span></h2>
  <div class="sec-rule" style="top:124px"></div>

  <article class="post" style="left:142px">
    <div class="thumb" role="img" aria-label="Photo of a desk with laptop, calculator and printed charts" style="background:linear-gradient(135deg,#dfe8f1,#9fb8d1 60%,#4f6f92)"></div>
    <div class="body"><h3>Advancing Actuarial Methods in a Changing Regulatory Landscape</h3><p>Exploring how modern tools support evolving best practices in reserving and capital modeling.</p><a class="learn">Learn More <svg width="16" height="10" viewBox="0 0 16 10"><path d="M1 5h13M10 1l4 4-4 4" stroke="#0677BA" stroke-width="1.6" fill="none"/></svg></a></div>
  </article>
  <article class="post" style="left:457px">
    <div class="thumb" role="img" aria-label="Photo of hands reviewing printed reports next to a laptop" style="background:linear-gradient(135deg,#C7EBF8,#6FCCEA 55%,#e8eef3)"></div>
    <div class="body"><h3>Governance and Documentation in Actuarial Modeling</h3><p>Why audit trails and assumption transparency are critical for internal and external review.</p><a class="learn">Learn More <svg width="16" height="10" viewBox="0 0 16 10"><path d="M1 5h13M10 1l4 4-4 4" stroke="#0677BA" stroke-width="1.6" fill="none"/></svg></a></div>
  </article>
  <article class="post" style="left:772px">
    <div class="thumb" role="img" aria-label="Photo of a professional working at a laptop in a dim office" style="background:linear-gradient(135deg,#132c48,#2e5176 55%,#5d8a7a)"></div>
    <div class="body"><h3>Multi-Jurisdictional Actuarial Practice: Challenges &amp; Solutions</h3><p>Strategies for managing compliance across Solvency II, NAIC, and emerging frameworks.</p><a class="learn">Learn More <svg width="16" height="10" viewBox="0 0 16 10"><path d="M1 5h13M10 1l4 4-4 4" stroke="#0677BA" stroke-width="1.6" fill="none"/></svg></a></div>
  </article>

  <a class="btn center-cta" style="left:515px;top:556px">Read Insights <span class="btn-arrow"><svg width="14" height="14" viewBox="0 0 14 14"><path d="M2 7h10M8 3l4 4-4 4" stroke="#fff" stroke-width="1.8" fill="none"/></svg></span></a>
</section>

<!-- call to action -->
<div class="cta-box" role="img" aria-label="Dark background photo of a person holding a phone with a glowing network globe">
  <h2 class="cta-title">READY TO SEE THE<br><b>PLATFORM IN ACTION?</b></h2>
  <p class="cta-text">Schedule a technical walkthrough and discover how QP Fiduciary can bring<br>structure, transparency, and auditability to your actuarial processes.</p>
  <a class="btn center-cta" style="left:307px;top:245px">Request A Technical Walkthrough <span class="btn-arrow"><svg width="14" height="14" viewBox="0 0 14 14"><path d="M2 7h10M8 3l4 4-4 4" stroke="#fff" stroke-width="1.8" fill="none"/></svg></span></a>
</div>

<footer class="site-footer">
  <div class="foot-brand"><span class="brand-dot" style="width:26px;height:26px"></span>QP Fiduciary</div>
  <p class="foot-about">Software that translates actuarial methodologies into disciplined, decision-ready analytical tools across diverse regulatory environments.</p>

  <h4 class="foot-head" style="left:576px;top:198px">QUICK LINKS</h4>
  <ul class="foot-links"><li>Home</li><li>Platform</li><li>Solutions</li><li>Insights</li><li>Company</li><li>Contact</li></ul>

  <h4 class="foot-head" style="left:813px;top:198px">CONTACT DETAILS</h4>
  <div class="contact-row" style="top:246px"><svg width="14" height="18" viewBox="0 0 14 18"><path d="M7 1a6 6 0 0 1 6 6c0 4-6 10-6 10S1 11 1 7a6 6 0 0 1 6-6z" fill="#fff"/><circle cx="7" cy="7" r="2.2" fill="#071d38"/></svg><div><span style="font-family:'Orbitron',sans-serif;color:#fff">QP FIDUCIARY, Inc.</span><br>410 Harbor Point Ave, Suite 12<br>Bayview, FL 30000</div></div>
  <div class="contact-row" style="top:334px"><svg width="16" height="16" viewBox="0 0 16 16"><path d="M3 1l3 0 1.5 4-2 1.5a9 9 0 0 0 4 4L11 8.5l4 1.5v3a2 2 0 0 1-2 2C7 15 1 9 1 3a2 2 0 0 1 2-2z" fill="#fff"/></svg><div style="color:#fff;font-size:14px">+1(555)010-2040</div></div>
  <div class="contact-row" style="top:384px"><svg width="16" height="12" viewBox="0 0 16 12"><rect width="16" height="12" rx="1" fill="#fff"/><path d="M1 1l7 6 7-6" stroke="#071d38" stroke-width="1.4" fill="none"/></svg><div>hello@qp-fiduciary.example</div></div>

  <div class="foot-rule"></div>
  <p class="foot-bottom">© 2026 QP Fiduciary. All rights reserved. &nbsp;&nbsp;&nbsp;&nbsp;&nbsp; Privacy · Terms</p>
  <div class="socials"><span></span><span></span><span></span></div>
</footer>

</body>
</html>
```